Employment Agency Website Design

We are working with an employment agency in California.

Some sites to use for content/competitors and inspiration:

https://www.pinecrestjobs.com/us/en
https://www.velmorusa.com
https://www.dravenworks.us
https://www.quillora.com/en
https://www.tomvalusa.com
https://www.fernstaffing.com

Thank you for taking the time to consider designing a website for us. We are web developers based in Stockton, CA, USA. Most of our projects go through the same process. Understanding this process may help you win a project with us. We custom-code all of our websites in-house. We don’t have any requirements as to what tools you use for your design, but we prefer Figma files. For any design that we label as four-stars, we send it to the client for review. The client picks the final design they want us to use. Once we complete this process, we will continue to show additional clients all the four-star sites and purchase them later. Your designs will have multiple chances to sell. For better chances of success, we ask that you follow these guidelines.

IMAGES:
If you use any images or icons in the design, we ask that you have a link to the asset so we can purchase the image/icon. Most of the designs we submit do not have the customer’s images on them unless they have some great images. Be creative; show us the feeling you are trying to portray with your image choices. Use any royalty-free site you choose. We subscribe to Adobe and mainly use their images, but we can purchase images outside of Adobe. PLEASE NOTE: we will not submit designs to clients with watermarks on the images.

FONTS:
We ask that you identify the fonts used in the design. This can be done in a message if you want. We typically use Google Fonts and Adobe Fonts.

CONTENT:
We're always open to different content and ideas. We often submit designs with stock images so the client can see our vision. We typically take pictures after the website launch to use their images with our vision. Lorem Ipsum is fine for paragraphs, but we ask that you write the headers in correct English. We want to be able to show the vision and identify the sections of the website.

INSPIRATION:
We typically add a couple of links in the brief of websites we like to help you get started in your design.

REVISIONS:
We do not often ask for revisions of the designs unless we see something in the design that may not appeal to the client. If there are slight changes that we want to make, we do that in the development process.

FEEDBACK:
We rarely give feedback on designs during the design process. We are working on many website projects and do not have the time to provide feedback. We usually respond if your request is well thought out and asks specific questions, but a note asking “feedback, please” usually goes unanswered.

```html
<!DOCTYPE html>
<html lang="en">
<head>
<meta charset="utf-8">
<title>Corvane Talent — Employment Agency</title>
<link href="https://fonts.googleapis.com/css2?family=Montserrat:wght@400;500;600;700&family=Open+Sans:wght@400;600&display=swap" rel="stylesheet">
<style>
:root{
  --red:#d3303c;
  --red-dark:#b8222d;
  --ink:#1f1f22;
  --text:#6d6d72;
  --pink:#fcf0f1;
  --grey:#efefef;
  --white:#ffffff;
  --footer:#222225;
}
*{box-sizing:border-box;margin:0;padding:0}
html,body{width:1200px;height:4756px;overflow:hidden;background:var(--white)}
body{position:relative;font-family:"Open Sans",Arial,sans-serif;color:var(--text)}
.abs{position:absolute}
h1,h2,h3,.brand,.nav,.btn{font-family:"Montserrat",Arial,sans-serif}
.btn{display:inline-block;background:var(--red);color:var(--white);font-size:13px;font-weight:600;letter-spacing:.5px;padding:12px 20px;text-transform:uppercase}
.btn.light{background:var(--white);color:var(--red)}
.para{font-size:14px;line-height:24px;color:var(--text)}
.photo{position:absolute}
/* header */
.brand{display:flex;align-items:center;gap:10px;font-weight:700;font-size:30px;color:var(--ink)}
.brand .dot{width:30px;height:30px;border-radius:50%;background:var(--red)}
.callbar{left:740px;top:0;width:460px;height:40px;background:var(--red);color:var(--white);font-size:14px;font-family:"Montserrat",Arial,sans-serif;display:flex;align-items:center;padding-left:70px;gap:8px;clip-path:polygon(6% 0,100% 0,100% 100%,0 100%)}
.nav{left:535px;top:48px;display:flex;gap:34px;font-size:15px;font-weight:500;color:var(--ink)}
/* hero */
.hero-photo{left:0;top:84px;width:1200px;height:436px;background:linear-gradient(120deg,#6c5a4a,#3e3530 55%,#8a7a6c)}
.hero-panel{left:0;top:84px;width:560px;height:436px;background:var(--red);clip-path:polygon(0 0,88% 0,100% 50%,88% 100%,0 100%)}
.hero-title{left:150px;top:150px;width:420px;color:var(--white);font-size:46px;line-height:54px;font-weight:700}
/* search */
.search{left:0;top:520px;width:1200px;height:120px;background:var(--grey)}
.search h2{position:absolute;left:140px;top:36px;font-size:40px;font-weight:500;color:var(--ink)}
.field{position:absolute;top:40px;height:44px;background:var(--white);font-size:13px;color:#999;padding:13px 14px}
/* sections */
h2.sec{font-size:40px;line-height:46px;color:var(--ink);font-weight:700}
h2.sec span{font-weight:400}
.pink{background:var(--pink)}
.red-band{left:0;top:2210px;width:1200px;height:760px;background:var(--red);clip-path:polygon(0 0,100% 0,100% 88%,50% 100%,0 88%)}
.step{position:absolute;top:3236px;width:240px;text-align:center}
.step p{font-size:17px;color:var(--ink);margin-top:14px;font-family:"Montserrat",Arial,sans-serif;font-weight:500}
.card h3{font-size:20px;line-height:26px;color:var(--ink);font-weight:500}
.card .date{font-size:12px;color:var(--ink);margin-bottom:8px}
.card .more{font-family:"Montserrat",Arial,sans-serif;color:var(--red);font-weight:600;font-size:13px;margin-top:12px}
.card .para{font-size:13px;line-height:20px}
/* footer */
.footer{left:0;top:4330px;width:1200px;height:426px;background:var(--footer)}
.footer h3{color:var(--white);font-size:20px;font-weight:700;letter-spacing:.5px}
.footer ul{list-style:none;color:#cfcfcf;font-size:13px;line-height:24px}
</style>
</head>
<body>

<!-- header -->
<div class="abs brand" style="left:140px;top:22px"><span class="dot"></span>Corvane Talent</div>
<div class="abs callbar">
  <svg width="16" height="16" viewBox="0 0 24 24" fill="#fff"><path d="M6.6 10.8a15 15 0 0 0 6.6 6.6l2.2-2.2a1 1 0 0 1 1-.25 11.4 11.4 0 0 0 3.6.57 1 1 0 0 1 1 1V20a1 1 0 0 1-1 1A17 17 0 0 1 3 4a1 1 0 0 1 1-1h3.5a1 1 0 0 1 1 1c0 1.25.2 2.45.57 3.57a1 1 0 0 1-.25 1z"/></svg>
  Call us: +1 555 014 2290
</div>
<nav class="abs nav"><span>Find Jobs</span><span>Hire Talent</span><span>Explore Consulting Solutions</span><span>Insights</span></nav>

<!-- hero -->
<div class="photo hero-photo" role="img" aria-label="Photo of a professional woman working on a laptop in an office"></div>
<div class="abs hero-panel"></div>
<h1 class="abs hero-title">Anything’s possible when you have the talent</h1>
<a class="abs btn" style="left:150px;top:392px;background:transparent;border:2px solid #fff">Find a Job</a>

<!-- search -->
<section class="abs search">
  <h2>Find A Job</h2>
  <div class="field" style="left:435px;width:250px">Job Title</div>
  <div class="field" style="left:700px;width:220px">Location</div>
  <a class="btn" style="position:absolute;left:935px;top:40px;height:44px">Find a Job</a>
</section>

<!-- intro -->
<svg class="abs" style="left:120px;top:690px" width="330" height="380" viewBox="0 0 330 380" role="img" aria-label="Hexagon framed photo of a modern office interior">
  <defs><linearGradient id="hexFill" x1="0" y1="0" x2="1" y2="1"><stop offset="0" stop-color="#8e1d24"/><stop offset="1" stop-color="#d3303c"/></linearGradient></defs>
  <polygon points="165,0 330,95 330,285 165,380 0,285 0,95" fill="url(#hexFill)"/>
</svg>
<h2 class="abs sec" style="left:625px;top:725px;font-weight:600">Creating limitless<br><span>Opportunities,</span><br>Together.</h2>
<p class="abs para" style="left:625px;top:895px;width:440px">Sed ut perspiciatis unde omnis iste natus error sit voluptatem accusantium doloremque laudantium, totam rem aperiam, eaque ipsa quae ab illo inventore veritatis et quasi architecto beatae vitae dicta sunt explicabo. Nemo enim ipsam voluptatem quia voluptas sit aspernatur aut odit aut fugit, sed quia consequuntur magni dolores eos qui ratione voluptatem sequi nesciunt.</p>
<a class="abs btn" style="left:625px;top:1060px">Read More</a>

<!-- temporary staffing -->
<div class="abs pink" style="left:0;top:1190px;width:600px;height:510px"></div>
<div class="photo" style="left:600px;top:1190px;width:600px;height:510px;background:linear-gradient(135deg,#8a9a9c,#4f5a5e 60%,#c0a88f)" role="img" aria-label="Photo of two colleagues smiling at a laptop in an office"></div>
<h2 class="abs sec" style="left:140px;top:1290px">Temporary <span>Staffing</span></h2>
<p class="abs para" style="left:140px;top:1375px;width:400px">Sed ut perspiciatis unde omnis iste natus error sit voluptatem accusantium doloremque laudantium, totam rem aperiam, eaque ipsa quae ab illo inventore veritatis et quasi architecto beatae vitae dicta sunt explicabo. Nemo enim ipsam voluptatem quia voluptas sit aspernatur aut odit aut fugit, sed quia consequuntur magni.</p>
<a class="abs btn" style="left:140px;top:1540px">Read More</a>

<!-- direct hire -->
<div class="photo" style="left:0;top:1700px;width:600px;height:510px;background:linear-gradient(135deg,#d9d4cf,#8c7d70 55%,#3c3430)" role="img" aria-label="Photo of a businesswoman shaking hands across a desk"></div>
<div class="abs pink" style="left:600px;top:1700px;width:600px;height:510px"></div>
<h2 class="abs sec" style="left:645px;top:1805px">Direct <span>Hire</span></h2>
<p class="abs para" style="left:645px;top:1880px;width:420px">Sed ut perspiciatis unde omnis iste natus error sit voluptatem accusantium doloremque laudantium, totam rem aperiam, eaque ipsa quae ab illo inventore veritatis et quasi architecto beatae vitae dicta sunt explicabo. Nemo enim ipsam voluptatem quia voluptas sit aspernatur aut odit aut fugit, sed quia consequuntur magni.</p>
<a class="abs btn" style="left:645px;top:2050px">Read More</a>

<!-- workforce -->
<div class="abs red-band"></div>
<h2 class="abs" style="left:0;top:2280px;width:1200px;text-align:center;color:#fff;font-size:40px;line-height:48px;font-weight:600">Helping you solve your workforce<br><span style="font-weight:400">challenges</span></h2>
<p class="abs para" style="left:290px;top:2405px;width:620px;text-align:center;color:#fde3e5">Sed ut perspiciatis unde omnis iste natus error sit voluptatem accusantium doloremque laudantium, totam rem aperiam, eaque ipsa quae ab illo inventore veritatis et quasi architecto beatae vitae dicta sunt explicabo nemo enim.</p>
<a class="abs btn light" style="left:542px;top:2510px">Read More</a>
<div class="photo" style="left:190px;top:2625px;width:820px;height:345px;background:linear-gradient(120deg,#2e3a45,#6b5d57 50%,#c5b3a1)" role="img" aria-label="Video still of a smiling woman shaking hands at an interview"></div>
<svg class="abs" style="left:562px;top:2760px" width="76" height="76" viewBox="0 0 76 76"><circle cx="38" cy="38" r="38" fill="#d3303c"/><polygon points="30,24 54,38 30,52" fill="#fff"/></svg>

<!-- how it works -->
<h2 class="abs" style="left:0;top:3160px;width:1200px;text-align:center;font-size:40px;color:var(--ink);font-weight:700">How it works</h2>
<svg class="abs" style="left:0;top:3230px" width="1200" height="140" viewBox="0 0 1200 140">
  <path d="M240 70 C360 10 440 10 560 70" stroke="#c9c9c9" stroke-width="2" stroke-dasharray="6 6" fill="none"/>
  <path d="M640 70 C760 130 840 130 960 70" stroke="#c9c9c9" stroke-width="2" stroke-dasharray="6 6" fill="none"/>
  <g fill="none" stroke="#d3303c" stroke-width="3">
    <circle cx="200" cy="70" r="48"/><circle cx="600" cy="70" r="48"/><circle cx="1000" cy="70" r="48"/>
  </g>
  <g font-family="Montserrat, Arial, sans-serif" font-size="84" font-weight="300" fill="#d3303c">
    <text x="140" y="100">1</text><text x="530" y="100">2</text><text x="930" y="100">3</text>
  </g>
  <g fill="#d3303c">
    <rect x="194" y="52" width="24" height="32" rx="2"/>
    <circle cx="590" cy="60" r="7"/><circle cx="612" cy="60" r="7"/><rect x="580" y="72" width="42" height="12" rx="6"/>
    <circle cx="990" cy="60" r="7"/><circle cx="1012" cy="60" r="7"/><rect x="980" y="72" width="42" height="12" rx="6"/>
  </g>
</svg>
<div class="step" style="left:60px"><p style="margin-top:140px">Describe your need</p></div>
<div class="step" style="left:480px"><p style="margin-top:140px">View matching<br>candidates</p></div>
<div class="step" style="left:880px"><p style="margin-top:140px">Connect with a recruiter<br>to consult and hire</p></div>

<!-- insights -->
<h2 class="abs" style="left:0;top:3610px;width:1200px;text-align:center;font-size:40px;color:var(--ink);font-weight:700">Hiring trends <span style="font-weight:400">and insights</span></h2>
<article class="abs card" style="left:130px;top:3695px;width:300px">
  <div class="photo" style="position:relative;width:300px;height:210px;background:linear-gradient(135deg,#f0c08a,#7a5a40 60%,#2e2a28)" role="img" aria-label="Photo of a team meeting at a window at sunset"></div>
  <div style="padding:18px 10px">
    <div class="date">Aug 2019</div>
    <h3>Sed ut perspiciatis unde omnis iste natus</h3>
    <p class="para" style="margin-top:10px">Omnis iste natus error sit voluptatem accusantium doloremque laudantium totam rem aperiam eaque ipsa quae.</p>
    <div class="more">READ MORE</div>
  </div>
</article>
<article class="abs card" style="left:450px;top:3695px;width:620px;display:flex;gap:22px">
  <div class="photo" style="position:relative;flex:0 0 240px;height:210px;background:linear-gradient(135deg,#6a7a80,#3b3533 60%,#b08f70)" role="img" aria-label="Photo of a smiling woman seated in an office"></div>
  <div style="padding-top:14px">
    <div class="date">Aug 2019</div>
    <h3>Sed ut perspiciatis unde omnis iste natus error</h3>
    <p class="para" style="margin-top:10px">Omnis iste natus error sit voluptatem accusantium doloremque laudantium totam rem aperiam eaque ipsa quae.</p>
    <div class="more">READ MORE</div>
  </div>
</article>
<article class="abs card" style="left:450px;top:3925px;width:620px;display:flex;gap:22px">
  <div class="photo" style="position:relative;flex:0 0 240px;height:210px;background:linear-gradient(135deg,#9a8570,#4d4540 55%,#c8b8a4)" role="img" aria-label="Photo of colleagues collaborating around a table"></div>
  <div style="padding-top:14px">
    <div class="date">Aug 2019</div>
    <h3>Sed ut perspiciatis unde omnis iste natus error</h3>
    <p class="para" style="margin-top:10px">Omnis iste natus error sit voluptatem accusantium doloremque laudantium totam rem aperiam eaque ipsa quae.</p>
    <div class="more">READ MORE</div>
  </div>
</article>
<a class="abs btn" style="left:505px;top:4236px">Load More Insights</a>

<!-- footer -->
<footer class="abs footer">
  <div class="brand" style="position:absolute;left:140px;top:150px;color:#fff;font-size:32px"><span class="dot"></span>Corvane Talent</div>
  <h3 style="position:absolute;left:480px;top:80px">SIGNUP NEWSLETTER</h3>
  <p style="position:absolute;left:480px;top:114px;width:330px;font-size:12px;color:#cfcfcf">Stay updated with the latest hiring news and job openings.</p>
  <div style="position:absolute;left:480px;top:146px;width:240px;height:36px;background:#fff;font-size:12px;color:#999;padding:10px 12px">Enter Email</div>
  <div class="btn" style="position:absolute;left:720px;top:146px;height:36px;padding:10px 16px;font-size:12px">Subscribe</div>
  <svg style="position:absolute;left:480px;top:210px" width="200" height="30" viewBox="0 0 200 30"><g fill="#fff"><circle cx="15" cy="15" r="13"/><circle cx="50" cy="15" r="13"/><circle cx="85" cy="15" r="13"/><circle cx="120" cy="15" r="13"/><circle cx="155" cy="15" r="13"/></g></svg>
  <h3 style="position:absolute;left:930px;top:80px">LINKS</h3>
  <ul style="position:absolute;left:930px;top:114px"><li>Browse Jobs</li><li>Contract Talent</li><li>Permanent Talent</li><li>Consulting Solutions</li></ul>
  <p style="position:absolute;left:0;top:385px;width:1200px;text-align:center;font-size:12px;color:#bdbdbd">© 2024 Corvane Talent All Rights Reserved | Privacy Policy | Terms of Use</p>
</footer>

</body>
</html>
```